Stonebridge Building and Projects business cards

A business card with watermark background (construction work)

Company logo attached

Home improvement projects
House renovations
Bathroom and kitchen renovations
House extensions
New builds and granny flats

Director Omar Haddani
(Phone number)
omar@sbpbuilding.com.au
(Instagram logo) sbp_building

```html
<!DOCTYPE html>
<html lang="en">
<head>
<meta charset="utf-8">
<title>Stonebridge Building and Projects – Business Cards</title>
<link rel="stylesheet" href="https://fonts.googleapis.com/css2?family=Montserrat:wght@500;600;700&family=Roboto:wght@400;500&display=swap">
<style>
  :root {
    --brand-blue: #1c74c6;
    --brand-blue-dark: #155fa6;
    --charcoal: #3f4449;
    --ink: #2b2e33;
    --paper: #f7f7f5;
    --white: #ffffff;
    --backdrop: #e4e5e7;
  }
  * { box-sizing: border-box; margin: 0; padding: 0; }
  html, body { width: 1200px; height: 1050px; overflow: hidden; }
  body { background: var(--backdrop); font-family: "Roboto", Arial, sans-serif; position: relative; }

  .card {
    position: absolute; width: 560px; height: 320px; border-radius: 22px;
    overflow: hidden; box-shadow: 0 14px 30px rgba(0,0,0,.18);
  }

  /* Front */
  .card-front { left: 80px; top: 170px; background: var(--brand-blue); color: var(--white); }
  .front-watermark {
    position: absolute; inset: 0;
    background: radial-gradient(circle at 30% 40%, rgba(255,255,255,.08), rgba(255,255,255,0) 60%);
  }
  .front-brand { position: absolute; left: 0; right: 0; top: 52px; text-align: center; }
  .brand-mark {
    display: inline-block; width: 18px; height: 18px; background: var(--white);
    vertical-align: middle; margin-right: 10px;
  }
  .brand-name {
    font-family: "Montserrat", Arial, sans-serif; font-weight: 700; font-size: 25px;
    vertical-align: middle;
  }
  .tagline {
    display: inline-block; margin-top: 12px; font-family: "Montserrat", Arial, sans-serif;
    font-weight: 600; font-size: 17px; border-bottom: 2px solid currentColor; padding-bottom: 2px;
  }
  .services-band {
    position: absolute; left: 0; right: 0; top: 178px; height: 64px; background: var(--charcoal);
    display: flex; flex-direction: column; justify-content: center; align-items: center; gap: 6px;
    font-size: 14px; letter-spacing: .2px;
  }
  .front-contacts {
    position: absolute; left: 0; right: 0; bottom: 30px; display: flex; justify-content: center;
    gap: 36px; font-size: 14px;
  }
  .contact { display: flex; align-items: center; gap: 8px; }
  .contact svg { width: 15px; height: 15px; flex: none; }

  /* Back */
  .card-back { left: 560px; top: 560px; background: var(--paper); color: var(--ink); }
  .back-strip { position: absolute; left: 0; top: 0; bottom: 0; width: 44px; background: var(--brand-blue); }
  .back-rule { position: absolute; left: 52px; top: 0; bottom: 0; width: 2px; background: var(--charcoal); }
  .back-brand { position: absolute; right: 40px; top: 34px; text-align: right; color: var(--brand-blue); }
  .back-brand .brand-mark { background: var(--brand-blue); }
  .back-brand .brand-name { font-size: 22px; }
  .back-brand .tagline { font-size: 14px; margin-top: 8px; }
  .back-divider { position: absolute; left: 90px; right: 40px; top: 140px; height: 1.5px; background: var(--brand-blue); }
  .person { position: absolute; left: 90px; top: 168px; }
  .person-name { font-family: "Montserrat", Arial, sans-serif; font-weight: 700; font-size: 22px; color: var(--brand-blue); }
  .person-role { font-size: 14px; margin-top: 2px; }
  .person-contacts { margin-top: 14px; display: flex; flex-direction: column; gap: 6px; font-size: 14px; }
  .company-contacts {
    position: absolute; left: 310px; top: 210px; display: flex; flex-direction: column; gap: 8px; font-size: 14px;
  }
  .card-back .contact svg { color: var(--brand-blue); }
</style>
</head>
<body>

<section class="card card-front" aria-label="Business card front">
  <div class="front-watermark" role="img" aria-label="Faint construction work watermark"></div>
  <div class="front-brand">
    <span class="brand-mark"></span><span class="brand-name">Stonebridge Building and Projects</span><br>
    <span class="tagline">Built on solid ground!</span>
  </div>
  <div class="services-band">
    <p>Home Improvement Projects &nbsp;|&nbsp; House Renovations &nbsp;|&nbsp; House Extensions</p>
    <p>Bathroom &amp; Kitchen Renovations &nbsp;|&nbsp; New Builds &amp; Granny Flats</p>
  </div>
  <div class="front-contacts">
    <span class="contact">
      <svg viewBox="0 0 16 16"><circle cx="8" cy="8" r="6.5" fill="none" stroke="currentColor" stroke-width="1.5"/></svg>
      sbp_building
    </span>
    <span class="contact">
      <svg viewBox="0 0 16 16" fill="none" stroke="currentColor" stroke-width="1.3"><circle cx="8" cy="8" r="6.5"/><ellipse cx="8" cy="8" rx="3" ry="6.5"/><path d="M1.5 8h13"/></svg>
      sbpbuilding.com.au
    </span>
  </div>
</section>

<section class="card card-back" aria-label="Business card back">
  <div class="back-strip"></div>
  <div class="back-rule"></div>
  <div class="back-brand">
    <span class="brand-mark"></span><span class="brand-name">Stonebridge Building and Projects</span><br>
    <span class="tagline">Built on solid ground!</span>
  </div>
  <div class="back-divider"></div>
  <div class="person">
    <p class="person-name">Omar Haddani</p>
    <p class="person-role">Managing Director</p>
    <div class="person-contacts">
      <span class="contact">
        <svg viewBox="0 0 16 16"><path d="M4 1.5l2.3 3-1.3 1.6a8 8 0 0 0 4.9 4.9l1.6-1.3 3 2.3-1.3 2.3C8 14 2 8 1.7 2.8z" fill="currentColor"/></svg>
        0400 318 276
      </span>
      <span class="contact">
        <svg viewBox="0 0 16 16"><circle cx="8" cy="8" r="6.5" fill="none" stroke="currentColor" stroke-width="1.5"/></svg>
        sbp_building
      </span>
    </div>
  </div>
  <div class="company-contacts">
    <span class="contact">
      <svg viewBox="0 0 16 16" fill="none" stroke="currentColor" stroke-width="1.3"><rect x="1.5" y="3.5" width="13" height="9"/><path d="M1.5 3.5L8 9l6.5-5.5"/></svg>
      omar@sbpbuilding.com.au
    </span>
    <span class="contact">
      <svg viewBox="0 0 16 16" fill="none" stroke="currentColor" stroke-width="1.3"><circle cx="8" cy="8" r="6.5"/><ellipse cx="8" cy="8" rx="3" ry="6.5"/><path d="M1.5 8h13"/></svg>
      www.sbpbuilding.com.au
    </span>
  </div>
</section>

</body>
</html>
```